real esate business card with company logo and name

we need a business card design for a real esate company

The company name is Walsh & Brand Pty Ltd, and we have our logo designed and will upload. We want classic or moden feel. Black or white background. looks more textured. Should include folowinginformations
Owen Walsh and Lucy Brand
Sales Agents & Onsite Manager
p: 07 5948 2063
F: 07 5948 2174
M:0431 857 219
3/42 Marlow Crescent, FERNLEA QLD 4213

We want this business card looks professonal. Thank you in advance.

Industry/Entity Type

Real Estate Agent

Contact Information for Business Card

Owen Walsh and Lucy Brand
Onsite Manager & Sales Agents
p: 07 5948 2063
M:0431 857 219

Font styles to use
Serif

Colors
000000
fbfbfb
333333
959595

Requirements
Must have
• company logo and name, black or white back ground

```html
<!DOCTYPE html>
<html lang="en">
<head>
<meta charset="utf-8">
<title>Walsh &amp; Brand Pty Ltd — Business Card</title>
<link rel="stylesheet" href="https://fonts.googleapis.com/css2?family=Lato:wght@400;700&family=Oswald:wght@400&display=swap">
<style>
  :root {
    --backdrop: #2b2b2b;
    --card: #000000;
    --mark: #6e6e70;
    --brand-text: #959595;
    --panel-light: #d0d0d2;
    --panel-grey: #707070;
    --divider: #1e1e1e;
    --ink: #000000;
    --ink-soft: #111111;
  }
  * { margin: 0; padding: 0; box-sizing: border-box; }
  html, body {
    width: 1200px;
    height: 1086px;
    overflow: hidden;
    background: var(--backdrop);
  }
  .sheet { position: relative; width: 1200px; height: 1086px; }

  .card {
    position: absolute;
    left: 254px;
    width: 677px;
    height: 387px;
    background: var(--card);
    overflow: hidden;
  }
  .card--front { top: 126px; }
  .card--back  { top: 586px; height: 385px; }

  .brand-mark {
    position: absolute;
    left: 50%;
    transform: translateX(-50%);
    background: var(--mark);
  }
  .card--front .brand-mark { top: 40px; width: 118px; height: 118px; }
  .card--back  .brand-mark { top: 62px; width: 190px; height: 190px; }

  .brand-name {
    position: absolute;
    left: 0;
    right: 0;
    text-align: center;
    font-family: "Oswald", sans-serif;
    font-weight: 400;
    color: var(--brand-text);
    text-transform: uppercase;
    letter-spacing: 0.5px;
    white-space: nowrap;
  }
  .card--front .brand-name { top: 186px; font-size: 22px; }
  .card--back  .brand-name { top: 298px; font-size: 36px; }

  .info-band {
    position: absolute;
    left: 0;
    top: 243px;
    width: 100%;
    height: 121px;
    display: flex;
  }
  .info-band__identity {
    width: 339px;
    background: var(--panel-light);
    text-align: right;
    padding: 6px 20px 0 0;
    font-family: "Lato", sans-serif;
    color: var(--ink);
  }
  .info-band__divider { width: 3px; background: var(--divider); }
  .info-band__contact {
    flex: 1;
    background: var(--panel-grey);
    padding: 5px 0 0 19px;
    font-family: "Lato", sans-serif;
    color: var(--ink-soft);
  }
  .agent-name { font-size: 29px; font-weight: 700; line-height: 1.15; }
  .agent-role { font-size: 21px; font-weight: 400; line-height: 1.2; }

  .contact-list { list-style: none; }
  .contact-list li {
    display: flex;
    align-items: center;
    font-size: 19px;
    line-height: 22.5px;
  }
  .contact-list svg { width: 14px; height: 14px; margin-right: 7px; fill: var(--ink-soft); }
  .address { margin-top: 5px; font-size: 16px; line-height: 20px; }
</style>
</head>
<body>
<main class="sheet">

  <section class="card card--front" aria-label="Business card front">
    <div class="brand-mark" aria-hidden="true"></div>
    <p class="brand-name">Walsh &amp; Brand Pty Ltd.</p>

    <div class="info-band">
      <div class="info-band__identity">
        <p class="agent-name">Owen Walsh</p>
        <p class="agent-role">Sales Agents</p>
      </div>
      <div class="info-band__divider"></div>
      <div class="info-band__contact">
        <ul class="contact-list">
          <li>
            <svg viewBox="0 0 14 14" aria-label="Mobile"><path d="M4 0h6a1.5 1.5 0 0 1 1.5 1.5v11A1.5 1.5 0 0 1 10 14H4a1.5 1.5 0 0 1-1.5-1.5v-11A1.5 1.5 0 0 1 4 0zm0 2v9h6V2zm3 9.6a.8.8 0 1 0 0 1.6.8.8 0 0 0 0-1.6z" fill-rule="evenodd"/></svg>
            0431 857 219
          </li>
          <li>
            <svg viewBox="0 0 14 14" aria-label="Phone"><path d="M1 4.5C1 3 3.5 2 7 2s6 1 6 2.5V6h-3V4.8H4V6H1zM3.5 7h7l1.5 5H2zm3.5 1.2a1.6 1.6 0 1 0 0 3.2 1.6 1.6 0 0 0 0-3.2z" fill-rule="evenodd"/></svg>
            07 5948 2063
          </li>
          <li>
            <svg viewBox="0 0 14 14" aria-label="Fax"><path d="M3.5 1h7v3.5h-7zM1 5.5h12v5h-2.5V9h-7v1.5H1zM4.5 10h5v3h-5z"/></svg>
            07 5948 2174
          </li>
        </ul>
        <p class="address">3/42 Marlow Crescent<br>FERNLEA QLD 4213</p>
      </div>
    </div>
  </section>

  <section class="card card--back" aria-label="Business card back">
    <div class="brand-mark" aria-hidden="true"></div>
    <p class="brand-name">Walsh &amp; Brand Pty Ltd.</p>
  </section>

</main>
</body>
</html>
```